Business Card Design Project

Business card based on attached logo

Todd Merrick
Todd@lorvantest.com
877-514-9073 ext. 318
Www.LorvanTest.com

Industry/Entity Type

Business

```html
<!DOCTYPE html>
<html lang="en">
<head>
<meta charset="utf-8">
<title>LorvanTest Business Cards</title>
<link href="https://fonts.googleapis.com/css2?family=Arimo:wght@400;700&display=swap" rel="stylesheet">
<style>
  :root {
    --red: #ec1c24;
    --ink: #231f20;
    --paper: #ffffff;
    --stage: #e9e7e4;
    --edge: rgba(0,0,0,0.18);
  }
  * { margin: 0; padding: 0; box-sizing: border-box; }
  html, body { width: 1200px; height: 715px; overflow: hidden; }
  body {
    background: var(--stage);
    font-family: "Arimo", Arial, sans-serif;
    position: relative;
  }
  .card {
    position: absolute;
    width: 508px;
    height: 290px;
    box-shadow: 0 2px 6px var(--edge);
    overflow: hidden;
  }
  .card--front { left: 51px; top: 36px; background: var(--paper); }
  .card--back-white { left: 623px; top: 36px; background: var(--paper); }
  .card--back-red { left: 47px; top: 379px; background: var(--red); }
  .card--back-black { left: 628px; top: 381px; background: var(--ink); }

  /* Front */
  .brand {
    position: absolute;
    left: 39px;
    top: 50px;
    display: flex;
    align-items: center;
    gap: 12px;
  }
  .brand__name {
    font-weight: 700;
    font-size: 46px;
    letter-spacing: -0.5px;
    color: var(--ink);
  }
  .brand__square {
    width: 22px; height: 22px;
    background: var(--red);
  }
  .holder {
    position: absolute;
    left: 38px;
    top: 214px;
    font-size: 21px;
    letter-spacing: 0.8px;
    color: var(--red);
  }
  .divider {
    position: absolute;
    left: 255px;
    top: 212px;
    width: 1.5px;
    height: 80px;
    background: var(--red);
  }
  .contacts {
    position: absolute;
    left: 274px;
    top: 213px;
    list-style: none;
    font-size: 13.5px;
    color: var(--ink);
  }
  .contacts li {
    display: flex;
    align-items: center;
    gap: 6px;
    height: 24px;
  }
  .contacts svg { width: 11px; height: 11px; flex: none; }

  /* Backs */
  .mark {
    position: absolute;
    left: 0; right: 0;
    top: 88px;
    display: flex;
    justify-content: center;
    align-items: center;
    gap: 14px;
  }
  .mark__name { font-weight: 700; font-size: 52px; letter-spacing: -0.5px; }
  .mark__square { width: 30px; height: 30px; }
  .card--back-white .mark__name { color: var(--red); }
  .card--back-white .mark__square { background: var(--red); }
  .card--back-red .mark__name,
  .card--back-black .mark__name { color: var(--paper); }
  .card--back-red .mark__square,
  .card--back-black .mark__square { background: var(--paper); }

  .url {
    position: absolute;
    left: 0; right: 0;
    text-align: center;
    font-size: 15.5px;
    letter-spacing: 3px;
  }
  .card--back-white .url { top: 262px; color: var(--ink); }
  .card--back-red .url { top: 264px; color: var(--paper); }
  .card--back-black .url { top: 266px; color: var(--paper); }
</style>
</head>
<body>

  <section class="card card--front" aria-label="Business card front">
    <div class="brand">
      <span class="brand__name">LorvanTest</span>
      <span class="brand__square"></span>
    </div>
    <p class="holder">Todd Merrick</p>
    <span class="divider"></span>
    <ul class="contacts">
      <li>
        <svg viewBox="0 0 12 12" aria-hidden="true"><path fill="var(--red)" d="M2.4 0.8 4.3 2.7 3.3 4.1c.7 1.6 2 2.9 3.6 3.6l1.4-1 1.9 1.9-1.4 1.8C5 10.2 1.8 7 .6 2.2z"/></svg>
        877-514-9073 ext. 318
      </li>
      <li>
        <svg viewBox="0 0 12 12" aria-hidden="true"><rect x="0.5" y="2.5" width="11" height="7.5" fill="var(--red)"/><path d="M0.8 2.8 6 7 11.2 2.8" fill="none" stroke="#fff" stroke-width="1"/></svg>
        Todd@lorvantest.com
      </li>
      <li>
        <svg viewBox="0 0 12 12" aria-hidden="true"><g fill="none" stroke="var(--red)" stroke-width="1"><circle cx="6" cy="6" r="5"/><ellipse cx="6" cy="6" rx="2.2" ry="5"/><path d="M1 6h10M2 3.3h8M2 8.7h8"/></g></svg>
        www.LorvanTest.com
      </li>
    </ul>
  </section>

  <section class="card card--back-white" aria-label="Business card back, white">
    <div class="mark"><span class="mark__name">LorvanTest</span><span class="mark__square"></span></div>
    <p class="url">www.LorvanTest.com</p>
  </section>

  <section class="card card--back-red" aria-label="Business card back, red">
    <div class="mark"><span class="mark__name">LorvanTest</span><span class="mark__square"></span></div>
    <p class="url">www.LorvanTest.com</p>
  </section>

  <section class="card card--back-black" aria-label="Business card back, black">
    <div class="mark"><span class="mark__name">LorvanTest</span><span class="mark__square"></span></div>
    <p class="url">www.LorvanTest.com</p>
  </section>

</body>
</html>
```